Brisk Harbor claims recovery services

Its a new company in Dubai UAE. The company activity is debt management, debt collection, loans settlements and restructuring. The company involved in any business or sector requires debt management including government entities, Medical & Health care sector, Banks & finance companies, SME's and commercial business.

Target Market(s)

government entities, Medical & Health care sector, Banks & finance companies, SME's and commercial business.

Industry/Entity Type

Financial Service

Number of Pages Required

5+ page

Requirements
Must have
• Focus on the services not the team and clients
Should not have
• Colorful . Shouldn't have Client testimonial and our clients

```html
<!DOCTYPE html>
<html lang="en">
<head>
<meta charset="utf-8">
<title>Brisk Harbor — About Us</title>
<link rel="stylesheet" href="https://fonts.googleapis.com/css2?family=Open+Sans:wght@300;400;600;700&family=Cinzel:wght@400;600&family=Roboto:wght@500&display=swap">
<style>
:root{
  --navy:#0d4d79;
  --navy-dark:#0a3f66;
  --accent:#1a5f8e;
  --ink:#555;
  --muted:#777;
  --rule:#e6e6e6;
  --band:#f3f4f6;
  --white:#fff;
}
*{box-sizing:border-box;margin:0;padding:0}
html,body{width:826px;height:1200px;overflow:hidden}
body{position:relative;background:var(--white);font-family:"Open Sans",sans-serif;color:var(--ink)}
.abs{position:absolute}

/* header */
.site-header{position:absolute;left:0;top:0;width:826px;height:78px}
.brand{left:67px;top:24px;display:flex;align-items:center;gap:9px}
.brand-mark{width:22px;height:22px;background:var(--navy);display:block}
.brand-name{font-size:20px;font-weight:400;color:var(--navy);letter-spacing:.5px}
.call{left:461px;top:27px;display:flex;align-items:center;gap:8px;font-size:8.5px;color:var(--muted)}
.call b{font-weight:600;color:var(--navy);font-size:10px}
.quote-btn{left:640px;top:25px;width:118px;height:29px;background:linear-gradient(#1b6a9d,var(--navy-dark));color:#fff;font-size:7.5px;font-weight:600;display:flex;align-items:center;justify-content:center;border-radius:2px}

/* nav */
.main-nav{left:0;top:78px;width:826px;height:36px;background:linear-gradient(#c9cbce,#a9acb0);display:flex;padding:0 68px}
.main-nav a{flex:1;display:flex;align-items:center;justify-content:center;height:36px;color:#fff;font-size:7.5px;text-decoration:none}
.main-nav a.active{background:var(--accent)}

/* hero */
.hero{left:0;top:114px;width:826px;height:263px;background:linear-gradient(100deg,#1c3550 0%,#28425d 45%,#1a2a3c 100%)}
.hero-glow{left:0;top:172px;width:826px;height:91px;background:linear-gradient(180deg,rgba(200,160,100,0) 0%,rgba(120,90,60,.35) 60%,rgba(10,15,25,.6) 100%)}
.hero-title{left:130px;top:104px;font-family:"Cinzel",serif;color:#fff}
.hero-title h1{font-size:20px;font-weight:600;letter-spacing:.5px}
.hero-title p{font-size:13px;margin-top:8px;letter-spacing:1px}
.arrow{top:112px}

/* about */
.about-title{left:0;top:405px;width:826px;text-align:center;font-size:18px;font-weight:600;color:var(--navy)}
.about-lead{left:190px;top:433px;width:446px;text-align:center;font-size:8.6px;line-height:17px;color:#666}
.about-photo{left:68px;top:487px;width:309px;height:200px;border:4px solid #eee;background:linear-gradient(120deg,#2e3e55,#6b86a6 55%,#c9d6e3)}
.copy{font-size:7.3px;line-height:17.6px;color:var(--muted)}
.copy-side{left:413px;top:493px;width:340px}
.copy-side p+p{margin-top:12px}
.copy-wide{left:68px;width:690px}

/* divider band */
.band{left:0;top:918px;width:826px;height:88px;background:var(--band);border-top:1px solid var(--rule)}

/* footer */
.site-footer{left:0;top:1006px;width:826px;height:194px;background:var(--navy);color:#fff}
.f-brand{left:67px;top:36px;display:flex;align-items:center;gap:8px}
.f-brand i{width:18px;height:18px;background:#fff;display:block}
.f-brand span{font-size:14px}
.f-about{left:67px;top:76px;width:145px;font-size:7.5px;line-height:16px}
.f-head{font-family:"Roboto",sans-serif;font-size:10.5px;font-weight:500}
.f-nav{left:256px;top:32px}
.f-nav ul{list-style:none;display:grid;grid-template-columns:47px auto;row-gap:6px;margin-top:10px;font-size:7.3px}
.f-news{left:405px;top:32px;width:180px}
.f-news p{font-size:7.3px;line-height:14.5px;margin-top:10px}
.signup{display:flex;margin-top:8px}
.signup .field{width:115px;height:26px;background:#0a4370;font-size:7px;color:#b5c8da;padding:8px 9px}
.signup .btn{width:55px;height:26px;background:#fff;color:var(--navy);font-size:10.5px;display:flex;align-items:center;justify-content:center}
.f-contact{left:629px;top:32px;width:140px}
.f-contact address{font-style:normal;font-size:7.8px;line-height:15.5px;margin-top:12px}
.f-line{display:flex;align-items:center;gap:12px;margin-top:8px}
.f-line.phone{font-size:11px}
.f-line.mail{font-size:8.5px}
.f-rule{left:67px;top:156px;width:692px;border-top:1px solid rgba(255,255,255,.12)}
.f-copy{left:67px;top:171px;font-size:7.5px}
.f-social{left:621px;top:164px;display:flex;align-items:center;gap:7px;font-size:7.5px}
.f-social i{width:18px;height:18px;border-radius:50%;background:#fff;display:block}
.f-social span{margin-right:3px}
</style>
</head>
<body>

<header class="site-header">
  <div class="abs brand"><i class="brand-mark"></i><span class="brand-name">Brisk Harbor</span></div>
  <div class="abs call">
    <svg width="24" height="24" viewBox="0 0 24 24"><circle cx="12" cy="12" r="11" fill="none" stroke="#0d4d79" stroke-width="1.2"/><path d="M9 7.5l1.6 2.4-1 1.1c.6 1.4 1.7 2.5 3.1 3.1l1.1-1 2.4 1.6-.9 1.7c-3.7-.3-6.7-3.3-7-7z" fill="#0d4d79"/></svg>
    Call Us Today : <b>(+100) 555-0142</b>
  </div>
  <div class="abs quote-btn">REQUEST A QUOTE</div>
</header>

<nav class="abs main-nav">
  <a>HOME</a><a class="active">ABOUT US</a><a>SERVICES</a><a>OUR TEAM</a><a>CONTACT US</a>
</nav>

<section class="abs hero" role="img" aria-label="Businessman's hand stopping a row of falling wooden dominoes on a dark desk">
  <div class="abs hero-glow"></div>
  <div class="abs hero-title">
    <h1>MANAGING YOUR MONEY</h1>
    <p>RECOVERING YOUR RELATIONSHIPS</p>
  </div>
  <svg class="abs arrow" style="left:38px" width="14" height="40" viewBox="0 0 14 40"><path d="M12 2L2 20l10 18" fill="none" stroke="rgba(255,255,255,.5)" stroke-width="1"/></svg>
  <svg class="abs arrow" style="left:772px" width="14" height="40" viewBox="0 0 14 40"><path d="M2 2l10 18L2 38" fill="none" stroke="rgba(255,255,255,.5)" stroke-width="1"/></svg>
</section>

<h2 class="abs about-title">ABOUT US</h2>
<p class="abs about-lead">Intelligent lending opens doors and allows ambitious individuals and fledgling businesses to grow. But without careful planning and management, debt can become overwhelming.</p>

<div class="abs about-photo" role="img" aria-label="Business people shaking hands in a bright office meeting"></div>

<div class="abs copy copy-side">
  <p>Ducimus qui blanditiis praesentium voluptatum deleniti atque corrupti quos dolores et quaser molestias excepturi sint occaecati cupiditate non provident, similique sunt in culpa qui officias deserunt mollitia animi, id est laborum et dolorum fuga. Et harum quidem rerum facilis est etto distinguish. In a free hour, when our power of choice is untrammelled and when nothingersers expedita distinctio Nam libero tempore, cum soluta nobis...</p>
  <p>same as saying through shrinking from toil and pain. These cases are perfectly simple and easy to distinguish. In a free hour, when our power of choice is untrammelled and when nothingers prevents our being able to do what we like best, every pleasure is to be welcomed and ipsums everyesto distinguish. In a free hour, when our power of choice is untrammelled and when nothingers &nbsp;pain avoided.circumstances and owing ...</p>
</div>

<p class="abs copy copy-wide" style="top:710px">Nothingers &nbsp;Nam libero tempore, cum soluta nobis est eligendi optio cumque nihil impedit quo minus id quod maxime placeat facere possimus, omnis voluptas assumenda est, omnis dolorem repellendus. Temporibus autem quibusdam et aut officiis debitis aut rerum necessitatibus saepe eveniet ut et voluptates repudiandae sint et molestiae non recusandae. Itaque earum rerum hic tenetur a sapiente delectus, ut aut reiciendis voluptatibus maiores alias consequatur we denounce with righteous indignation and dislike men who are so beguiled and demoralized by theers charms of pleasure of the moment, so blinded by desire, that they cannot foresee the pain and trouble that are bound to ensue; and equal blame belongs to those who fail in their duty through weakness of will, which is the same as saying through shrinking from toil and pain. These cases are perfectly simple and easy to distinguish. In a free hour...</p>

<p class="abs copy copy-wide" style="top:816px">Repellendus. Temporibus autem quibusdam et aut officiis debitis aut rerum necessitatibus saepe eveniet ut et voluptates repudiandae sint et molestiae non recusandae. Itaque earum rerum hic tenetur a sapiente delectus, ut aut reiciendis voluptatibus maiores alias consequatur we denounce with righteous indignation and dislike men who are so beguiled and demoralized by theers charms of pleasure of the moment, so blinded by desire, that they cannot foresee the pain and trouble that are bound to ensue; and equal blame belongs to those who fail in their duty through weakness of will, which is the same as saying through shrinking from toil and pain. These cases are perfectly simple and easy to distinguish. In a free hour...</p>

<div class="abs band"></div>

<footer class="abs site-footer">
  <div class="abs f-brand"><i></i><span>Brisk Harbor</span></div>
  <p class="abs f-about">Sed ut perspiciatis unde omnis isteers accusantium doloremque laudantium, totam rem aperiam, eaque ipsa quae ab illo inventore veritatis et...</p>

  <div class="abs f-nav">
    <h3 class="f-head">NAVIGATION</h3>
    <ul><li>Home</li><li>Team</li><li>About Us</li><li>Contact Us</li><li>Services</li></ul>
  </div>

  <div class="abs f-news">
    <h3 class="f-head">NEWSLETTER</h3>
    <p>Excepteur sint occaecat cupidatat non proident, sunt in culpa qui officia deserunt mollit anim enim ipsam voluptatem quia...</p>
    <div class="signup"><div class="field">Enter your email address</div><div class="btn">Sign Up</div></div>
  </div>

  <div class="abs f-contact">
    <h3 class="f-head">CONTACT US</h3>
    <address>Office 12, Harbor Tower;<br>Creek Road;City-1020</address>
    <div class="f-line phone">
      <svg width="14" height="14" viewBox="0 0 24 24"><path d="M5 3l4 5-2 2c1.2 2.8 3.2 4.8 6 6l2-2 5 4-2 3C10 20 4 14 3 5z" fill="none" stroke="#fff" stroke-width="1.5"/></svg>
      (900) 555-0187
    </div>
    <div class="f-line mail">
      <svg width="14" height="11" viewBox="0 0 14 11"><rect x=".5" y=".5" width="13" height="10" fill="none" stroke="#fff"/><path d="M.5 .5L7 6l6.5-5.5" fill="none" stroke="#fff"/></svg>
      hello@briskharbor.example
    </div>
  </div>

  <div class="abs f-rule"></div>
  <p class="abs f-copy">Copyrights©briskharbor.2016 | Allrights Reserved.</p>
  <div class="abs f-social"><span>Connect With Us:</span><i></i><i></i><i></i></div>
</footer>

</body>
</html>
```